BildeVOLD buisnesscard

Hey :) I need a modern buisnesscard for my company BildeVOLD
It most have:
Dagligleder og Fotograf: Henrik Audun Strandvik

Mob: +4791264085
Epost: post@bildevold.example
Adresse: Kvernbakken9, 6040 Langevåg

Facbook and instagram logo with text BildeVOLD

BildeVOLD logo

It Company

```html
<!DOCTYPE html>
<html lang="no">
<head>
<meta charset="utf-8">
<title>BildeVOLD – visittkort</title>
<link href="https://fonts.googleapis.com/css2?family=Questrial&display=swap" rel="stylesheet">
<style>
  :root {
    --backdrop: #8a7b80;
    --plum: #5f0e44;
    --plum-light: #6c1752;
    --navy: #0f3a63;
    --navy-light: #13477a;
    --ink: #ffffff;
    --ink-soft: rgba(255,255,255,0.88);
  }
  * { box-sizing: border-box; margin: 0; padding: 0; }
  html, body { width: 1200px; height: 675px; overflow: hidden; }
  body {
    background: var(--backdrop);
    font-family: "Questrial", "Century Gothic", sans-serif;
    color: var(--ink);
    display: flex;
    align-items: center;
    justify-content: center;
    gap: 40px;
  }
  .card {
    position: relative;
    width: 540px;
    height: 309px;
    overflow: hidden;
    box-shadow: 0 10px 24px rgba(0,0,0,0.28);
  }
  .card-front { background: var(--plum); }
  .card-back { background: var(--navy); }
  .card-shapes { position: absolute; inset: 0; }

  .brand {
    display: flex;
    align-items: center;
    justify-content: center;
    gap: 8px;
    letter-spacing: 0.5px;
  }
  .brand-mark {
    width: 14px; height: 14px;
    background: var(--ink);
  }
  .card-front .brand {
    position: absolute; top: 40px; left: 0; right: 0;
    font-size: 24px;
  }
  .identity {
    position: absolute; top: 110px; left: 0; right: 0;
    text-align: center;
  }
  .person-name { font-size: 31px; font-weight: 400; }
  .person-role { font-size: 19px; margin-top: 6px; color: var(--ink-soft); }

  .contact-row {
    position: absolute; left: 24px; right: 24px; bottom: 34px;
    display: flex; justify-content: space-between;
    font-size: 12.5px;
  }
  .contact-item { display: flex; align-items: center; gap: 6px; }
  .contact-item svg { width: 12px; height: 12px; fill: var(--ink); }

  .card-back .brand {
    position: absolute; top: 118px; left: 0; right: 0;
    font-size: 46px; gap: 14px;
  }
  .card-back .brand-mark { width: 26px; height: 26px; border-radius: 50%; }
  .social-row {
    position: absolute; left: 0; right: 0; bottom: 30px;
    display: flex; justify-content: center; gap: 36px;
    font-size: 13px;
  }
  .social-item { display: flex; align-items: center; gap: 6px; }
  .social-dot { width: 11px; height: 11px; border-radius: 50%; background: var(--ink); }
</style>
</head>
<body>
  <section class="card card-front">
    <svg class="card-shapes" viewBox="0 0 540 309" preserveAspectRatio="none" aria-hidden="true">
      <polygon points="0,190 540,60 540,130 0,309" fill="var(--plum-light)"/>
      <polygon points="0,240 540,110 540,118 0,250" fill="var(--plum)" opacity="0.6"/>
    </svg>
    <div class="brand"><span class="brand-mark"></span>BildeVOLD</div>
    <div class="identity">
      <h1 class="person-name">Henrik Audun Strandvik</h1>
      <p class="person-role">Dagligleder og Fotograf</p>
    </div>
    <div class="contact-row">
      <span class="contact-item">
        <svg viewBox="0 0 24 24"><path d="M6.6 10.8a15 15 0 0 0 6.6 6.6l2.2-2.2c.3-.3.7-.4 1-.2 1.1.4 2.3.6 3.6.6.6 0 1 .4 1 1V20c0 .6-.4 1-1 1C10.6 21 3 13.4 3 4c0-.6.4-1 1-1h3.5c.6 0 1 .4 1 1 0 1.3.2 2.5.6 3.6.1.3 0 .7-.2 1z"/></svg>
        +4791264085
      </span>
      <span class="contact-item">
        <svg viewBox="0 0 24 24"><path d="M2 5h20v14H2z M3 6l9 7 9-7" fill="none" stroke="#fff" stroke-width="2"/></svg>
        post@bildevold.example
      </span>
      <span class="contact-item">
        <svg viewBox="0 0 24 24"><path d="M21 3 3 10.5l7.5 3 3 7.5z"/></svg>
        Kvernbakken9, 6040 Langevåg
      </span>
    </div>
  </section>

  <section class="card card-back">
    <svg class="card-shapes" viewBox="0 0 540 309" preserveAspectRatio="none" aria-hidden="true">
      <path d="M540,0 L540,120 C420,80 300,20 260,0 Z" fill="var(--navy-light)"/>
      <path d="M0,309 L0,200 C90,230 160,280 190,309 Z" fill="var(--navy-light)" opacity="0.7"/>
    </svg>
    <div class="brand"><span class="brand-mark"></span>BildeVOLD</div>
    <div class="social-row">
      <span class="social-item"><span class="social-dot"></span>BildeVOLD</span>
      <span class="social-item"><span class="social-dot"></span>BildeVOLD</span>
    </div>
  </section>
</body>
</html>
```